Detail Shop Business card design

i need a business card design for my new detailing company called 'Brisk's Polish Works'. i want an all black and white design . simple, direct and to the point. i want the designer to choose a fitting font to match the logothe front should have logo, address, phone and email and the back side should have a slogan and text indicating that we offer services on anything including cars, trucks, motorcycles and RVs. slogan will read "we take pride in your ride"
maybe also very small on the back side the IG icon with Brisks_Polish_Works

phone 208.417.6352
address 3847 E Larkin Ave
Spokane WA 99214
email: BrisksPolish@mailvexo.com

Target Market(s)

all ages , auto enthusiasts

Industry/Entity Type

Automotive

Contact Information for Business Card

the front should have logo, address, phone and email and the back side should have a slogan and text indicating that we offer services on anything including cars, trucks, motorcycles and RVs. slogan will read "we take pride in your ride"

phone 208.417.6352
address 3847 E Larkin Ave
Spokane WA 99214

Colors
000000
ffffff

Requirements
Must have
• bold font and very simple design with good spacing
Nice to have
• anything creative from the designer indicating we service any types of vehicles
Should not have
• any colors ,

```html
<!DOCTYPE html>
<html lang="en">
<head>
<meta charset="utf-8">
<title>Brisk's Polish Works – Business Card</title>
<link href="https://fonts.googleapis.com/css2?family=Arvo:ital,wght@0,400;0,700;1,400&family=Roboto+Slab:wght@800&display=swap" rel="stylesheet">
<style>
  :root {
    --ink: #000000;
    --paper: #ffffff;
    --backdrop: #d9d9d9;
    --edge: rgba(0,0,0,0.18);
  }
  html, body {
    margin: 0;
    padding: 0;
    width: 1200px;
    height: 835px;
    overflow: hidden;
    background: var(--backdrop);
  }
  .stage {
    position: relative;
    width: 1200px;
    height: 835px;
  }
  .card {
    position: absolute;
    top: 264px;
    width: 530px;
    height: 303px;
    background: var(--paper);
    box-shadow: 0 2px 10px var(--edge);
    color: var(--ink);
    font-family: "Arvo", serif;
  }
  .card--info { left: 50px; }
  .card--brand { left: 620px; }

  .brand-mark {
    display: flex;
    align-items: center;
    gap: 10px;
    font-family: "Arvo", serif;
    font-weight: 700;
    color: var(--ink);
    white-space: nowrap;
  }
  .brand-mark__dot {
    border-radius: 50%;
    background: var(--ink);
    flex: none;
  }
  .card--brand .brand-mark {
    position: absolute;
    left: 50%;
    top: 50%;
    transform: translate(-50%, -50%);
    font-size: 30px;
  }
  .card--brand .brand-mark__dot { width: 30px; height: 30px; }

  .slogan {
    position: absolute;
    left: 34px;
    top: 30px;
    margin: 0;
    font-family: "Roboto Slab", serif;
    font-weight: 800;
    font-size: 22px;
    line-height: 1.02;
    text-transform: uppercase;
    letter-spacing: 0.2px;
  }
  .services {
    position: absolute;
    left: 34px;
    top: 82px;
    width: 250px;
    margin: 0;
    font-size: 11.5px;
    line-height: 1.3;
  }
  .contacts {
    position: absolute;
    left: 34px;
    top: 150px;
    margin: 0;
    padding: 0;
    list-style: none;
    font-style: italic;
    font-size: 14px;
    line-height: 1;
  }
  .contacts li {
    display: flex;
    align-items: center;
    gap: 12px;
    margin-bottom: 14px;
  }
  .contacts svg, .address svg { flex: none; }
  .social-dot {
    width: 12px;
    height: 12px;
    border-radius: 50%;
    border: 2px solid var(--ink);
    box-sizing: border-box;
    flex: none;
  }
  .card--info .brand-mark {
    position: absolute;
    right: 30px;
    top: 150px;
    font-size: 17px;
    gap: 8px;
  }
  .card--info .brand-mark__dot { width: 16px; height: 16px; }
  .address {
    position: absolute;
    right: 30px;
    bottom: 26px;
    display: flex;
    align-items: flex-start;
    gap: 12px;
    font-weight: 700;
    font-size: 15px;
    line-height: 1.3;
  }
  .address svg { margin-top: 2px; }
</style>
</head>
<body>
<main class="stage">
  <section class="card card--info" aria-label="Card side with contact details">
    <h1 class="slogan">We take pride<br>in your ride</h1>
    <p class="services">We offer services on anything including cars, trucks, motorcycles and RVs.</p>
    <ul class="contacts">
      <li>
        <svg width="12" height="14" viewBox="0 0 12 14" aria-hidden="true"><path d="M3 0.5 L5 3.5 L3.6 5 C4.4 7 5.2 8.6 6.8 9.8 L8.4 8.6 L11 11 L9 13.5 C4 12.5 0.8 7 0.8 2.4 Z" fill="var(--ink)"/></svg>
        <span>208.417.6352</span>
      </li>
      <li>
        <svg width="14" height="11" viewBox="0 0 14 11" aria-hidden="true"><rect x="0" y="0" width="14" height="11" fill="var(--ink)"/><path d="M0.8 0.8 L7 6 L13.2 0.8" stroke="var(--paper)" stroke-width="1.2" fill="none"/></svg>
        <span>BrisksPolish@mailvexo.com</span>
      </li>
      <li>
        <span class="social-dot" aria-hidden="true"></span>
        <span>Brisks_Polish_Works</span>
      </li>
    </ul>
    <div class="brand-mark">
      <span class="brand-mark__dot" aria-hidden="true"></span>
      <span>Brisk's Polish Works</span>
    </div>
    <div class="address">
      <svg width="11" height="16" viewBox="0 0 11 16" aria-hidden="true"><path d="M5.5 0 C2.5 0 0 2.4 0 5.4 C0 9.4 5.5 16 5.5 16 C5.5 16 11 9.4 11 5.4 C11 2.4 8.5 0 5.5 0 Z" fill="var(--ink)"/><circle cx="5.5" cy="5.4" r="2.1" fill="var(--paper)"/></svg>
      <span>3847 E Larkin Ave<br>Spokane WA 99214</span>
    </div>
  </section>

  <section class="card card--brand" aria-label="Card side with brand name">
    <div class="brand-mark">
      <span class="brand-mark__dot" aria-hidden="true"></span>
      <span>Brisk's Polish Works</span>
    </div>
  </section>
</main>
</body>
</html>
```